VORN Paradigm. the way you communicate in every situation and in all environments.

I would like you to create a diagram depicting a very specific process of communication. it must follow the look of the diagram that i have attached. this is going to be used in a book called BRAVELL. it is going to explain the fact that we communicate all the same way using this process as we communicate. it starts with the fact that everyone takes everything that is said personally and then moves on to filters, which is your own agenda or experience kicking in. then you move to your why it matters, which is your motivation and ends with the choice of words you use when you communicate. if you are going to be successful then you must separate the person from the issue.

Target Market(s)

market is executive business people around the world

Industry/Entity Type

Consulting

Font styles to use
Sans Serif

Colors

Designer to choose only greyscale colors for use in the design.

Requirements
Must have
• I would like it to have a diving/ocean/snorkel feel to it. The analogy we are using is to make a deep dive when you are communicating. it must have every part of the diagram you see, it starts at the top with the vorn paradigm (and the words) it then connects to the filters which connects to the why it matters with connects to the words and then end with the separating the person from the issue.
Nice to have
• we are writing a black and white book NO color. therefore the words should be clear and easy to read. Each section should be able to stand on its own so we can write about it separately.
Should not have
• the diagram DOES NOT have to look like the one i gave you. it must explain the fact that it starts with VORN and ends with Separate and must pass through the three areas to get to the SEPARATE.

```html
<!DOCTYPE html>
<html lang="en">
<head>
<meta charset="utf-8">
<title>VORN Paradigm – 5 Steps Diagram</title>
<link rel="stylesheet" href="https://fonts.googleapis.com/css2?family=Bebas+Neue&family=Quicksand:wght@500;600&family=Montserrat:wght@400;500&display=swap">
<style>
  :root {
    --paper: #ffffff;
    --ink: #1b1b1b;
    --road-blue-start: #12b3dc;
    --road-blue-end: #0a7ccc;
    --step-blue: #39a7e0;
    --road-dark-start: #1b1830;
    --road-dark-end: #3c3c3c;
    --step-dark: #3b3b3b;
    --lane: #ffffff;
  }
  html, body {
    margin: 0;
    padding: 0;
    width: 1200px;
    height: 1200px;
    overflow: hidden;
    background: var(--paper);
  }
  .canvas { display: block; width: 1200px; height: 1200px; }
  .diagram-title {
    font-family: "Bebas Neue", sans-serif;
    font-size: 62px;
    fill: var(--ink);
    text-anchor: middle;
  }
  .road-lane { fill: none; stroke: var(--lane); stroke-width: 2.2; stroke-dasharray: 14 9; }
  .flow-arrow { fill: var(--lane); }
  .step-heading {
    font-family: "Quicksand", sans-serif;
    font-weight: 600;
    font-size: 22px;
    fill: var(--lane);
    text-anchor: middle;
  }
  .step-text {
    font-family: "Montserrat", sans-serif;
    font-size: 13.4px;
    fill: var(--lane);
    text-anchor: middle;
  }
  .diagram--color .step-disc { fill: var(--step-blue); }
  .diagram--color .end-arrow { fill: var(--road-blue-end); }
  .diagram--mono .step-disc { fill: var(--step-dark); }
  .diagram--mono .end-arrow { fill: var(--road-dark-end); }
</style>
</head>
<body>
<svg class="canvas" viewBox="0 0 1500 1500" xmlns="http://www.w3.org/2000/svg" xmlns:xlink="http://www.w3.org/1999/xlink">
  <defs>
    <linearGradient id="road-blue" x1="0" y1="0" x2="1" y2="0">
      <stop offset="0" stop-color="var(--road-blue-start)"/>
      <stop offset="1" stop-color="var(--road-blue-end)"/>
    </linearGradient>
    <linearGradient id="road-dark" x1="0" y1="0" x2="1" y2="0">
      <stop offset="0" stop-color="var(--road-dark-start)"/>
      <stop offset="1" stop-color="var(--road-dark-end)"/>
    </linearGradient>
    <path id="road-path" fill="none"
      d="M 322.3 542.8
         A 133.5 133.5 0 1 1 353.5 457
         A 133.5 133.5 0 0 0 620.5 457
         A 133.5 133.5 0 0 1 887.5 457
         A 133.5 133.5 0 0 0 1154.5 457
         A 133.5 133.5 0 1 1 1205.8 562.2"/>
    <g id="flow-arrows" class="flow-arrow">
      <polygon points="342,466 365,466 353.5,488"/>
      <polygon points="609,456 632,456 620.5,434"/>
      <polygon points="876,454 899,454 887.5,476"/>
      <polygon points="1143,454 1166,454 1154.5,432"/>
    </g>
    <polygon id="end-arrow-shape" points="1186.1,587.4 1225.5,537.0 1170.3,534.5"/>
  </defs>

  <!-- Colour diagram -->
  <text class="diagram-title" x="750" y="128">5 Steps Diagram - Color Version- Vector Format</text>
  <g class="diagram diagram--color">
    <use href="#road-path" stroke="url(#road-blue)" stroke-width="34"/>
    <use href="#road-path" class="road-lane"/>
    <use href="#end-arrow-shape" class="end-arrow"/>
    <use href="#flow-arrows"/>

    <g class="step">
      <circle class="step-disc" cx="220" cy="457" r="102"/>
      <text class="step-heading" x="218" y="440">VORN Paradigm</text>
      <text class="step-text" x="218" y="466">When words are taken</text>
      <text class="step-text" x="218" y="487">personally, what happens?</text>
    </g>
    <g class="step">
      <circle class="step-disc" cx="487" cy="457" r="102"/>
      <text class="step-heading" x="485" y="440">Your Filters</text>
      <text class="step-text" x="485" y="466">An accumulation of your</text>
      <text class="step-text" x="485" y="487">experience, knowleldge</text>
      <text class="step-text" x="485" y="508">and vvalues</text>
    </g>
    <g class="step">
      <circle class="step-disc" cx="754" cy="457" r="102"/>
      <text class="step-heading" x="752" y="440">Why It Matters</text>
      <text class="step-text" x="752" y="466">This is your compass.</text>
      <text class="step-text" x="752" y="487">It is what motivattes you,</text>
      <text class="step-text" x="752" y="508">what drive you.</text>
    </g>
    <g class="step">
      <circle class="step-disc" cx="1021" cy="457" r="102"/>
      <text class="step-heading" x="1022" y="440">Your Words</text>
      <text class="step-text" x="1022" y="466">This is your immediate</text>
      <text class="step-text" x="1022" y="487">response, verbal or perhaps</text>
      <text class="step-text" x="1022" y="508">non-verbal</text>
    </g>
    <g class="step">
      <circle class="step-disc" cx="1288" cy="457" r="102"/>
      <text class="step-heading" x="1289" y="440">What To Do</text>
      <text class="step-text" x="1289" y="466">Separate the Person from</text>
      <text class="step-text" x="1289" y="487">the Issue</text>
    </g>
  </g>

  <!-- Greyscale diagram -->
  <text class="diagram-title" x="750" y="818">5 Steps Diagram -Black &amp; White Version- Vector Format</text>
  <g class="diagram diagram--mono" transform="translate(7 614)">
    <use href="#road-path" stroke="url(#road-dark)" stroke-width="34"/>
    <use href="#road-path" class="road-lane"/>
    <use href="#end-arrow-shape" class="end-arrow"/>
    <use href="#flow-arrows"/>

    <g class="step">
      <circle class="step-disc" cx="220" cy="457" r="102"/>
      <text class="step-heading" x="218" y="440">VORN Paradigm</text>
      <text class="step-text" x="218" y="466">When words are taken</text>
      <text class="step-text" x="218" y="487">personally, what happens?</text>
    </g>
    <g class="step">
      <circle class="step-disc" cx="487" cy="457" r="102"/>
      <text class="step-heading" x="485" y="440">Your Filters</text>
      <text class="step-text" x="485" y="466">An accumulation of your</text>
      <text class="step-text" x="485" y="487">experience, knowleldge</text>
      <text class="step-text" x="485" y="508">and vvalues</text>
    </g>
    <g class="step">
      <circle class="step-disc" cx="754" cy="457" r="102"/>
      <text class="step-heading" x="752" y="440">Why It Matters</text>
      <text class="step-text" x="752" y="466">This is your compass.</text>
      <text class="step-text" x="752" y="487">It is what motivattes you,</text>
      <text class="step-text" x="752" y="508">what drive you.</text>
    </g>
    <g class="step">
      <circle class="step-disc" cx="1021" cy="457" r="102"/>
      <text class="step-heading" x="1022" y="440">Your Words</text>
      <text class="step-text" x="1022" y="466">This is your immediate</text>
      <text class="step-text" x="1022" y="487">response, verbal or perhaps</text>
      <text class="step-text" x="1022" y="508">non-verbal</text>
    </g>
    <g class="step">
      <circle class="step-disc" cx="1288" cy="457" r="102"/>
      <text class="step-heading" x="1289" y="440">What To Do</text>
      <text class="step-text" x="1289" y="466">Separate the Person from</text>
      <text class="step-text" x="1289" y="487">the Issue</text>
    </g>
  </g>
</svg>
</body>
</html>
```